Business Card Design

New business card design

Target Market(s)

Residential & Commercial Property Managers

Industry/Entity Type

Plumbing Services

Contact Information for Business Card

Name - Rowan Keddle, title - Director, Phone Number - 0431 286 517, email - rowan@tbk-plumbing.com.au, Company ABN - 73 215 904 386,

Font styles to use
Sans Serif

Colors
0054AA
0677BA
7BADD7
CADEEF
E8F1F8

```html
<!DOCTYPE html>
<html lang="en">
<head>
<meta charset="utf-8">
<title>TBK Plumbing Services – Business Card</title>
<link href="https://fonts.googleapis.com/css2?family=Montserrat:wght@400;500;600&display=swap" rel="stylesheet">
<style>
  :root {
    --backdrop: #1b1c1e;
    --card-white: #f4f4f4;
    --card-dark: #1d232a;
    --accent-blue: #2aa0da;
    --ink: #1f262d;
    --white: #ffffff;
  }
  * { margin: 0; padding: 0; box-sizing: border-box; }
  html, body {
    width: 1200px; height: 1059px; overflow: hidden;
    background: var(--backdrop);
    font-family: "Montserrat", sans-serif;
  }
  .canvas { position: relative; width: 1200px; height: 1059px; }
  .card {
    position: absolute; width: 690px; height: 392px;
    border-radius: 24px; overflow: hidden;
  }
  .card-front { left: 256px; top: 89px; background: var(--card-white); }
  .card-back { left: 254px; top: 547px; background: var(--card-dark); }

  .front-wave { position: absolute; left: 0; top: 0; width: 690px; height: 392px; }

  .brand {
    position: absolute; display: flex; align-items: center;
    font-weight: 500; white-space: nowrap;
  }
  .brand-dot { border-radius: 50%; background: var(--accent-blue); flex: none; }
  .card-front .brand {
    left: 50px; width: 270px; top: 181px; gap: 9px;
    font-size: 19px; line-height: 24px; color: var(--ink);
  }
  .card-front .brand-dot { width: 13px; height: 13px; }

  .divider {
    position: absolute; left: 344px; top: 121px; width: 1.5px; height: 150px;
    background: var(--accent-blue);
  }
  .contact { position: absolute; left: 372px; top: 117px; color: var(--ink); }
  .contact-name { font-size: 26px; font-weight: 600; color: var(--accent-blue); line-height: 30px; }
  .contact-title { font-size: 17px; font-weight: 400; line-height: 22px; }
  .contact-abn { margin-top: 18px; font-size: 18px; line-height: 22px; }
  .contact-abn .label { color: var(--accent-blue); }
  .contact-line {
    display: flex; align-items: center; gap: 8px;
    font-size: 17.5px; line-height: 26px;
  }
  .contact-phone { margin-top: 18px; }
  .contact-line svg { width: 13px; height: 13px; flex: none; }

  .card-back .brand {
    left: 0; right: 0; top: 176px; justify-content: center; gap: 12px;
    font-size: 34px; line-height: 40px; color: var(--white);
  }
  .card-back .brand-dot { width: 22px; height: 22px; }
</style>
</head>
<body>
<div class="canvas">
  <section class="card card-front">
    <svg class="front-wave" viewBox="0 0 690 392" aria-hidden="true">
      <path d="M0 322 C120 370 240 378 420 350 C540 332 620 320 690 352 L690 392 L0 392 Z" fill="var(--card-dark)"/>
      <path d="M0 322 C120 370 240 372 420 340 C540 318 620 310 690 342 L690 352 C620 320 540 328 420 348 C240 372 120 368 0 324 Z" fill="var(--accent-blue)"/>
    </svg>
    <div class="brand"><span class="brand-dot"></span>TBK Plumbing Services</div>
    <div class="divider"></div>
    <div class="contact">
      <div class="contact-name">Rowan Keddle</div>
      <div class="contact-title">Director</div>
      <div class="contact-abn"><span class="label">ABN</span> - 73 215 904 386</div>
      <div class="contact-line contact-phone">
        <svg viewBox="0 0 24 24"><path fill="var(--accent-blue)" d="M6.6 10.8a15.1 15.1 0 0 0 6.6 6.6l2.2-2.2c.3-.3.7-.4 1-.2 1.1.4 2.3.6 3.6.6.6 0 1 .4 1 1V20c0 .6-.4 1-1 1A17 17 0 0 1 3 4c0-.6.4-1 1-1h3.5c.6 0 1 .4 1 1 0 1.3.2 2.5.6 3.6.1.3 0 .7-.2 1z"/></svg>
        0431 286 517
      </div>
      <div class="contact-line">
        <svg viewBox="0 0 24 24"><path fill="var(--accent-blue)" d="M2 5h20v14H2z"/><path d="M2 5l10 8 10-8M2 19l7-7M22 19l-7-7" stroke="var(--card-white)" stroke-width="1.6" fill="none"/></svg>
        rowan@tbk-plumbing.com.au
      </div>
    </div>
  </section>

  <section class="card card-back">
    <div class="brand"><span class="brand-dot"></span>TBK Plumbing Services</div>
  </section>
</div>
</body>
</html>
```